Brightfield Ventures Inc. Letterhead

Creation of attractive and eye catching letterhead for a business start-up for the construction industry. Letterhead must relate to construction, but avoid standard hammer and tools in the design.

I forgot to add some details, sorry about that. Some pertinent info: Ph: 916-555-0187 brightfieldventures.example 448 Willowmere Ave, Ste 210 Folsom, CA 95999 info@brightfieldventures.example not sure if slogan should be in there" “Connecting construction professionals to create a purpose driven industry.” must be able to be used in word. Thanks!

```html
<!DOCTYPE html>
<html lang="en">
<head>
<meta charset="utf-8">
<title>Brightfield Ventures Inc. Letterhead</title>
<link href="https://fonts.googleapis.com/css2?family=Lato:wght@400;700&family=Kaushan+Script&display=swap" rel="stylesheet">
<style>
  :root {
    --navy: #1c2157;
    --red: #c8202a;
    --text: #4a4a4a;
    --ink: #222222;
    --paper: #ffffff;
  }
  * { margin: 0; padding: 0; box-sizing: border-box; }
  html, body { width: 909px; height: 1200px; overflow: hidden; background: var(--paper); }
  .letterhead {
    position: relative;
    width: 909px;
    height: 1200px;
    background: var(--paper);
    font-family: 'Lato', sans-serif;
    color: var(--text);
  }
  .header-band { position: absolute; top: 0; left: 0; width: 909px; height: 70px; }
  .brand-name {
    position: absolute;
    top: 96px;
    left: 0;
    width: 909px;
    text-align: center;
    font-weight: 700;
    font-size: 23px;
    line-height: 28px;
    letter-spacing: 2px;
    color: var(--navy);
  }
  .address, .contact {
    position: absolute;
    top: 115px;
    font-size: 12.5px;
    line-height: 20px;
    color: var(--text);
    white-space: nowrap;
  }
  .address { right: 688px; text-align: right; }
  .address-rule, .contact-rule {
    position: absolute;
    top: 116px;
    width: 2px;
    height: 36px;
    background: var(--red);
  }
  .address-rule { left: 233px; }
  .contact-rule { left: 630px; }
  .contact { left: 642px; }
  .contact-line { display: flex; align-items: center; gap: 4px; }
  .contact-line svg { width: 10px; height: 10px; flex: none; }
  .letter-body {
    position: absolute;
    top: 229px;
    left: 76px;
    width: 755px;
  }
  .salutation {
    font-weight: 700;
    font-size: 16.5px;
    line-height: 22px;
    color: var(--navy);
    margin-bottom: 24px;
  }
  .paragraph { margin-bottom: 21px; font-size: 16.5px; line-height: 27.2px; }
  .paragraph .line {
    display: block;
    text-align: justify;
    text-align-last: justify;
    white-space: nowrap;
  }
  .paragraph .line.last { text-align-last: left; }
  .closing {
    font-size: 19px;
    line-height: 24px;
    color: var(--ink);
    margin-top: 24px;
  }
  .signature {
    font-family: 'Kaushan Script', cursive;
    font-size: 31px;
    line-height: 40px;
    color: var(--navy);
    margin-top: 8px;
  }
  .footer {
    position: absolute;
    top: 1162px;
    left: 0;
    width: 909px;
    display: flex;
    justify-content: center;
    align-items: center;
    gap: 10px;
    font-size: 14px;
    letter-spacing: 1px;
    color: var(--text);
  }
  .footer-rule { width: 45px; height: 2px; background: var(--red); }
  .footer strong { color: var(--navy); font-weight: 700; }
</style>
</head>
<body>
  <main class="letterhead">
    <svg class="header-band" viewBox="0 0 909 70" aria-hidden="true">
      <polygon points="0,0 909,0 909,54 454.5,3 0,54" fill="var(--navy)"/>
      <polyline points="0,62 454.5,7 909,62" fill="none" stroke="var(--red)" stroke-width="3"/>
    </svg>

    <div class="brand-name">BRIGHTFIELD VENTURES</div>

    <div class="address">
      <div>448 Willowmere Ave, Ste 210</div>
      <div>Folsom, CA 95999</div>
    </div>
    <span class="address-rule"></span>

    <span class="contact-rule"></span>
    <div class="contact">
      <div class="contact-line">
        <svg viewBox="0 0 10 10" aria-hidden="true"><path d="M2 1 L4 1 L4.6 3.2 L3.4 4 Q4.4 6 6 6.6 L6.8 5.4 L9 6 L9 8 Q8.6 9 7.5 9 Q1 8 1 2.5 Q1 1 2 1 Z" fill="var(--red)"/></svg>
        <span>916-555-0187</span>
      </div>
      <div class="contact-line">
        <svg viewBox="0 0 10 10" aria-hidden="true"><rect x="1" y="2.5" width="8" height="6" fill="var(--red)"/><polyline points="1,2.8 5,6 9,2.8" fill="none" stroke="#fff" stroke-width="1"/></svg>
        <span>info@brightfieldventures.example</span>
      </div>
    </div>

    <section class="letter-body">
      <p class="salutation">Dear Mr. Lorem,</p>
      <p class="paragraph">
        <span class="line">Lorem ipsum dolor sit amet, consectetuer adipiscing elit, sed diam nonummy nibh euismod tinci-</span>
        <span class="line">dunt ut laoreet dolore magna aliquam erat volutpat. Ut wisi enim ad minim veniam, quis nostrud</span>
        <span class="line">exerci tation ullamcorper suscipit lobortis nisl ut aliquip ex ea commodo consequat. Duis autem vel</span>
        <span class="line">eum iriure dolor in hendiusto odio dignissim qui blandit praesent luptatum zzril delenit augue duis</span>
        <span class="line last">dolore te feugait nulla facilisi.</span>
      </p>
      <p class="paragraph">
        <span class="line">Lorem ipsum dolor sit amet, consectetuer adipiscing elit, sed diam nonummy nibh euismod tinci-</span>
        <span class="line">dunt ut laoreet dolore magna aliquam erat volutpat. Ut wisi enim ad minim veniam, quis nostrud</span>
        <span class="line">exerci tation ullamcorper suscipit lobortis nisl ut aliquip ex ea commodo consequat. Duis autem vel</span>
        <span class="line">eum iriure dolor in hendiusto odio dignissim qui blandit praesent luptatum zzril delenit augue duis</span>
        <span class="line last">dolore te feugait nulla facilisi.</span>
      </p>
      <p class="paragraph">
        <span class="line">Lorem ipsum dolor sit amet, consectetuer adipiscing elit, sed diam nonummy nibh euismod tinci-</span>
        <span class="line">dunt ut laoreet dolore magna aliquam erat volutpat. Ut wisi enim ad minim veniam, quis nostrud</span>
        <span class="line">exerci tation ullamcorper suscipit lobortis nisl ut aliquip ex ea commodo consequat. Duis autem vel</span>
        <span class="line">eum iriure dolor in hendiusto odio dignissim qui blandit praesent luptatum zzril delenit augue duis</span>
        <span class="line last">dolore te feugait nulla facilisi.</span>
      </p>
      <p class="closing">Sincerely Your,</p>
      <p class="signature">Your Name</p>
    </section>

    <footer class="footer">
      <span class="footer-rule"></span>
      <span>www.<strong>brightfieldventures</strong>.example</span>
      <span class="footer-rule"></span>
    </footer>
  </main>
</body>
</html>
```